Book Cover with this title and sub title
Where Auntie Found Her Quiet Orchard
The little book to be smart with your money and help the environment.
Walter P. Brunk Ph. D.
Ellen R. Brunk
Picture below would be on the entire front cover. Words somehow incorporated for easy reading.

```html
<!DOCTYPE html>
<html lang="en">
<head>
<meta charset="utf-8">
<title>Where Auntie Found Her Quiet Orchard — Cover Spread</title>
<link href="https://fonts.googleapis.com/css2?family=Work+Sans:wght@500;600;700&display=swap" rel="stylesheet">
<style>
  :root{
    --page:#ffffff;
    --ink:#ffffff;
    --black:#000000;
    --back-dark:#050505;
    --back-mid:#1a1a1a;
    --spine:#0b0b0b;
    --photo-yellow:#f2b70f;
    --photo-orange:#d98a06;
    --photo-green:#3d4a2a;
    --photo-dark:#1c1a12;
  }
  *{box-sizing:border-box;margin:0;padding:0}
  html,body{width:1200px;height:1200px;overflow:hidden;background:var(--page)}
  body{font-family:"Work Sans",Arial,sans-serif;color:var(--ink);position:relative}
  .spread{
    position:absolute;left:30px;top:202px;width:1140px;height:795px;
    display:flex;
  }
  .back-cover{
    width:532px;height:100%;
    background:radial-gradient(ellipse at 50% 85%,var(--back-mid) 0%,var(--back-dark) 60%,var(--black) 100%);
    padding:66px 38px 0;text-align:center;
  }
  .back-title{font-weight:600;font-size:29px;line-height:1.05;letter-spacing:-0.3px}
  .back-subtitle{font-weight:600;font-size:15px;line-height:1.45;margin-top:14px}
  .back-blurb{
    font-weight:600;font-size:11.6px;line-height:17.2px;text-align:justify;
    margin-top:16px;
  }
  .back-blurb + .back-blurb{margin-top:17px}
  .spine{
    width:80px;height:100%;background:var(--spine);
    display:flex;flex-direction:column;align-items:center;justify-content:space-between;
    padding:52px 0 40px;
  }
  .spine-title,.spine-authors{
    writing-mode:vertical-rl;font-weight:600;white-space:nowrap;
  }
  .spine-title{font-size:22px;letter-spacing:-0.2px}
  .spine-authors{font-size:19px;line-height:1.2;text-align:left}
  .front-cover{position:relative;width:528px;height:100%;overflow:hidden}
  .cover-photo{
    position:absolute;inset:0;
    background:
      radial-gradient(ellipse 62% 48% at 58% 60%,var(--photo-yellow) 0%,var(--photo-orange) 45%,rgba(217,138,6,0) 72%),
      linear-gradient(180deg,var(--photo-green) 0%,var(--photo-dark) 35%,var(--photo-dark) 70%,var(--black) 100%);
  }
  .front-text{position:relative;text-align:center;height:100%;
    text-shadow:0 2px 6px rgba(0,0,0,.55)}
  .front-title{font-weight:700;font-size:52px;line-height:1.02;letter-spacing:-1px;padding-top:48px}
  .front-subtitle{font-weight:600;font-size:17px;line-height:1.3;margin:16px auto 0;width:420px}
  .front-authors{position:absolute;left:0;right:0;bottom:40px;font-weight:600;font-size:34px;line-height:1.42}
</style>
</head>
<body>
  <main class="spread">
    <section class="back-cover">
      <h2 class="back-title">Where Auntie<br>Found Her Quiet<br>Orchard</h2>
      <p class="back-subtitle">The little book to be smart with your money and<br>help the environment</p>
      <p class="back-blurb">Lorem ipsum dolor sit amet, consectetur adipiscing elit, sed do eiusmod tempor incididunt ut labore et dolore magna aliqua. Quis ipsum suspendisse ultrices gravida. Risus commodo viverra maecenas accumsan lacus vel facilisis. Lorem ipsum dolor sit amet, consectetur adipiscing elit, sed do eiusmod tempor incididunt ut labore et dolore magna aliqua. Quis ipsum suspendisse ultrices gravida. Risus commodo viverra maecenas accumsan lacus vel facilisis. Lorem ipsum dolor sit amet, consectetur adipiscing elit, sed do eiusmod tempor incididunt ut labore et dolore magna aliqua. Quis ipsum suspendisse ultrices gravida. Risus commodo viverra maecenas accumsan lacus vel facilisis.</p>
      <p class="back-blurb">Lorem ipsum dolor sit amet, consectetur adipiscing elit, sed do eiusmod tempor incididunt ut labore et dolore magna aliqua. Quis ipsum suspendisse ultrices gravida. Risus commodo viverra maecenas accumsan lacus vel facilisis. Lorem ipsum dolor sit amet, consectetur adipiscing elit, sed do eiusmod tempor incididunt ut labore et dolore magna aliqua. Quis ipsum suspendisse ultrices gravida. Risus commodo viverra maecenas accumsan lacus vel facilisis. Lorem ipsum dolor sit amet, consectetur adipiscing elit, sed do eiusmod tempor incididunt ut labore et dolore magna aliqua. Quis ipsum suspendisse ultrices gravida. Risus commodo viverra maecenas accumsan lacus vel facilisis. Lorem ipsum dolor sit amet, consectetur adipiscing elit, sed do eiusmod tempor incididunt ut labore et dolore magna aliqua. Quis ipsum suspendisse ultrices gravida. Risus commodo viverra maecenas accumsan lacus vel facilisis. Quis ipsum suspendisse ultrices gravida. Risus commodo viverra maecenas accumsan lacus vel facilisis.</p>
    </section>
    <section class="spine">
      <span class="spine-title">Where Auntie Found Her Quiet Orchard</span>
      <span class="spine-authors">Walter P. Brunk Ph. D.<br>Ellen R. Brunk</span>
    </section>
    <section class="front-cover">
      <div class="cover-photo" role="img" aria-label="Close-up photograph of a honeybee gathering pollen on a bright yellow dandelion against dark green foliage"></div>
      <div class="front-text">
        <h1 class="front-title">Where Auntie<br>Found Her Quiet<br>Orchard</h1>
        <p class="front-subtitle">The little book to be smart with your money and help the environment</p>
        <p class="front-authors">Walter P. Brunk Ph. D.<br>Ellen R. Brunk</p>
      </div>
    </section>
  </main>
</body>
</html>
```